Stationery Design Project

Our company is "Meridian Systems" and we have a product called "lunogrid.com". The product is an online accounting software for businesses. We want to communicate that our software will help business owners to be more efficient and help them track their finances better. Lunogrid.com is basically a simple version of ledgerpal.

"We want a unique and creative design which will surprise our customer."

NAME CARD = LUNOGRID
We want a lunogrid name card NOT MERIDIAN SYSTEMS.

For the content of the name card, please make sure it fit with a long name like the following:

Rudi Wahyo Alias Rudi
Developer Specialist
T: (021) 4827 1036
F: (021) 4827 1037
E: customer.service@mrdn-sys.example

I need you to put it the following information to the name card

"lunogrid"
- moto is "automate your businesses"
- website "www.lunogrid.com"
- lunogrid is a "Web Accounting Software"
- product of "Meridian Systems"

LETTERHEAD, ENVELOPE, FOLDER = MERIDIAN SYSTEMS
Other than name card we wanted you to design for us; letterhead, envelope and folder. In letterhead, envelope and folder it should ONLY contain the following information ("Meridian Systems").
PLEASE BE SURE YOU ARE NOT PUTTING "LUNOGRID LOGO" IN LETTERHEAD, ENVELOPE AND FOLDER.

"Meridian Systems"
Address:
Ruko Graha Pelangi Blok. D No. 18
Jl. Kenanga Raya No. 71
Jakarta
Cempaka, 11470
Indonesia

Web Address: mrdn-sys.example

T: (021) 4827 1036
F: (021) 4827 1037

Target Market(s)

Business Owners, Accountant, Auditor, Tax Consultant

Industry/Entity Type

Accounting

Requirements

```html
<!DOCTYPE html>
<html lang="en">
<head>
<meta charset="utf-8">
<title>Meridian Systems — Envelope</title>
<link rel="stylesheet" href="https://fonts.googleapis.com/css2?family=Open+Sans:wght@400;600&display=swap">
<style>
  :root {
    --backdrop: #eeeff1;
    --paper: #f7f7f8;
    --paper-edge: #e2e3e6;
    --ink: #4d4f53;
    --ink-soft: #6b6e73;
    --band-light: #b3cde3;
    --band-text: #2f6fa5;
    --flap-blue: #176ba8;
    --mark-green: #6a9a3a;
  }
  * { margin: 0; padding: 0; box-sizing: border-box; }
  html, body {
    width: 1200px;
    height: 795px;
    overflow: hidden;
    background: var(--backdrop);
    font-family: "Open Sans", Arial, sans-serif;
  }
  .canvas {
    position: relative;
    width: 1200px;
    height: 795px;
  }
  .envelope {
    position: absolute;
    width: 620px;
    height: 290px;
    background: var(--paper);
    border: 1px solid var(--paper-edge);
    box-shadow: 0 6px 18px rgba(0, 0, 0, 0.08);
    overflow: hidden;
  }
  .envelope--back {
    left: 520px;
    top: 90px;
  }
  .envelope--front {
    left: 60px;
    top: 405px;
  }
  .flap {
    position: absolute;
    left: 0;
    top: 0;
    width: 100%;
    height: 82px;
    background: var(--flap-blue);
    border-bottom-right-radius: 6px;
  }
  .sender {
    position: absolute;
    left: 28px;
    top: 26px;
    width: 320px;
  }
  .brand {
    display: flex;
    align-items: center;
    gap: 10px;
    height: 38px;
  }
  .brand__dot {
    width: 30px;
    height: 30px;
    border-radius: 50%;
    background: var(--mark-green);
    flex: none;
  }
  .brand__name {
    font-size: 21px;
    font-weight: 600;
    letter-spacing: 0.06em;
    color: var(--ink);
  }
  .web-band {
    margin-top: 8px;
    margin-left: -28px;
    width: 348px;
    height: 18px;
    background: var(--band-light);
    display: flex;
    align-items: center;
    justify-content: flex-end;
    padding-right: 12px;
  }
  .web-band__url {
    font-size: 11px;
    color: var(--band-text);
  }
  .address {
    margin-top: 8px;
    font-size: 9.5px;
    line-height: 1.45;
    color: var(--ink-soft);
    font-style: normal;
  }
</style>
</head>
<body>
  <main class="canvas">
    <section class="envelope envelope--back" aria-label="Envelope back">
      <div class="flap"></div>
    </section>

    <section class="envelope envelope--front" aria-label="Envelope front">
      <div class="sender">
        <div class="brand">
          <span class="brand__dot"></span>
          <span class="brand__name">MERIDIAN SYSTEMS</span>
        </div>
        <div class="web-band"><span class="web-band__url">mrdn-sys.example</span></div>
        <address class="address">
          Ruko Graha Pelangi Blok. D No. 18<br>
          Jl. Kenanga Raya No. 71<br>
          Jakarta, Cempaka, 11470, Indonesia
        </address>
      </div>
    </section>
  </main>
</body>
</html>
```